Business Card Design - Property Management & Real Estate Services

I need a business card design for my company that I can print ZEPLA Cards. The company is called Brindle Management Company. It is a property management and real estate company. The design has to be clean and modern. I need two versions. One for my employee and one for me. However, the design will be the same, just different text. You can get a feel for the company by looking at our website at www.brindlemanagement.example.

Industry/Entity Type

Property Management

Contact Information for Business Card

I will be using ZEPLA.com to print my cards. I will most likely use the rounded edges card. I need two versions, however, they will be the same design. I need one for me and my employee.

Colors
3276b5
33a6d7

Requirements
Must have
• Company Logo
• Name of person
• Property Management & Real Estate Service
• Phone
• Email
• Website
• Address
• A space to place a QR code

```html
<!DOCTYPE html>
<html lang="en">
<head>
<meta charset="utf-8">
<title>Brindle Management – Business Card</title>
<link href="https://fonts.googleapis.com/css2?family=Roboto:wght@400;500&family=Saira+Condensed:wght@600&display=swap" rel="stylesheet">
<style>
  :root {
    --bg: #c9c9c9;
    --card: #ffffff;
    --brand-dark: #2350a6;
    --brand-light: #5b8fd0;
    --text: #3c3c3c;
    --muted: #5a5a5a;
    --faint: #f1f2f4;
    --qr-line: #c4cddc;
  }
  * { box-sizing: border-box; margin: 0; padding: 0; }
  html, body { width: 1200px; height: 852px; overflow: hidden; }
  body {
    background: var(--bg);
    font-family: "Roboto", Arial, sans-serif;
    position: relative;
  }
  .card {
    position: absolute;
    top: 277px;
    width: 520px;
    height: 298px;
    background: var(--card);
    border-radius: 18px;
    overflow: hidden;
    box-shadow: 0 6px 16px rgba(0,0,0,0.18);
  }
  .card--front { left: 50px; }
  .card--back { left: 630px; }

  /* Front */
  .brand {
    position: absolute;
    left: 0; right: 0; top: 62px;
    display: flex;
    justify-content: center;
    align-items: center;
    gap: 14px;
  }
  .brand-mark {
    width: 44px; height: 44px;
    background: var(--brand-light);
    border-radius: 4px;
  }
  .brand-name {
    color: var(--brand-dark);
    font-weight: 500;
    line-height: 1;
  }
  .brand-name .word-main {
    display: block;
    font-size: 44px;
    letter-spacing: 2px;
  }
  .brand-name .word-sub {
    display: block;
    font-size: 12px;
    letter-spacing: 9px;
    margin-top: 6px;
    padding-left: 3px;
  }
  .front-service {
    position: absolute;
    left: 0; right: 0; top: 150px;
    text-align: center;
    font-size: 12px;
    letter-spacing: 0.5px;
    color: var(--muted);
  }
  .front-web {
    position: absolute;
    left: 0; right: 0; top: 214px;
    display: flex;
    justify-content: center;
    align-items: center;
    gap: 12px;
    font-size: 13px;
    color: var(--text);
  }
  .front-web .rule { width: 34px; height: 2px; background: var(--brand-light); }
  .front-band {
    position: absolute;
    left: 0; right: 0; bottom: 0;
    height: 10px;
    display: flex;
  }
  .front-band .band-light { flex: 1; background: var(--brand-light); }
  .front-band .band-dark { flex: 1; background: var(--brand-dark); }

  /* Back */
  .back-watermark {
    position: absolute;
    left: 228px; top: 70px;
    width: 170px; height: 190px;
    background: var(--faint);
    border-radius: 4px;
  }
  .person {
    position: absolute;
    left: 34px; top: 178px;
  }
  .person-name {
    font-family: "Saira Condensed", "Arial Narrow", sans-serif;
    font-weight: 600;
    font-size: 24px;
    color: var(--brand-dark);
    line-height: 1.1;
  }
  .person-role {
    font-size: 13px;
    color: var(--muted);
    margin-top: 3px;
  }
  .contact-list {
    position: absolute;
    left: 232px; top: 58px;
    list-style: none;
    font-size: 12.5px;
    color: var(--text);
    line-height: 19px;
  }
  .contact-list li { display: flex; align-items: center; gap: 7px; }
  .contact-list svg { width: 12px; height: 12px; flex: none; fill: var(--brand-dark); }
  .contact-list .no-icon { padding-left: 19px; }
  .qr-space {
    position: absolute;
    right: 30px; bottom: 28px;
    width: 82px; height: 82px;
    border: 1.5px dashed var(--qr-line);
    border-radius: 6px;
  }
</style>
</head>
<body>
  <section class="card card--front" aria-label="Card front">
    <div class="brand">
      <span class="brand-mark" aria-hidden="true"></span>
      <div class="brand-name">
        <span class="word-main">BRINDLE</span>
        <span class="word-sub">MANAGEMENT</span>
      </div>
    </div>
    <div class="front-service">Property Management &amp; Real Estate Services</div>
    <div class="front-web">
      <span class="rule"></span>
      <span>www.brindlemanagement.example</span>
      <span class="rule"></span>
    </div>
    <div class="front-band"><span class="band-light"></span><span class="band-dark"></span></div>
  </section>

  <section class="card card--back" aria-label="Card back">
    <div class="back-watermark" role="img" aria-label="Faint brand decoration area"></div>
    <ul class="contact-list">
      <li>
        <svg viewBox="0 0 24 24" aria-hidden="true"><path d="M6.6 10.8a15 15 0 0 0 6.6 6.6l2.2-2.2a1 1 0 0 1 1-.25 11.4 11.4 0 0 0 3.6.57 1 1 0 0 1 1 1V20a1 1 0 0 1-1 1A17 17 0 0 1 3 4a1 1 0 0 1 1-1h3.5a1 1 0 0 1 1 1c0 1.25.2 2.45.57 3.57a1 1 0 0 1-.25 1z"/></svg>
        (555) 010-0147
      </li>
      <li>
        <svg viewBox="0 0 24 24" aria-hidden="true"><path d="M2 5h20v14H2z M2 5l10 8 10-8"/></svg>
        marisol@brindlemanagement.example
      </li>
      <li>
        <svg viewBox="0 0 24 24" aria-hidden="true"><circle cx="12" cy="12" r="10"/></svg>
        www.brindlemanagement.example
      </li>
      <li class="no-icon">480 Harbor View Rd #210 Bayside, FL 30000</li>
    </ul>
    <div class="person">
      <div class="person-name">Marisol T. Avery</div>
      <div class="person-role">Founder</div>
    </div>
    <div class="qr-space" role="img" aria-label="Space reserved for QR code"></div>
  </section>
</body>
</html>
```